Business Card for a mobile physiotherapy company

I need a layout for a business card for a mobile physiotherapy company.
Slogan is "Mobile Physiotherapy - Your Road To Recovery"
Phone number is 867-555-0142
Email VardenTherapy@postnest.ca (subject to change with website)
Website www.VardenTherapy.ca
My name and credentials: Luke Varden Luke Varden, BSc(kin), MPT, CAFCI, IMS
Information maybe included: Direct Billing, Services including Physiotherapy, IMS, acupuncture
Maybe include facebook and instagram logos
One side with the logo clean and sharp
Other side with details, try not to look too busy, keep everything concise

```html
<!DOCTYPE html>
<html lang="en">
<head>
<meta charset="utf-8">
<title>Varden Therapy – Business Card</title>
<link rel="stylesheet" href="https://fonts.googleapis.com/css2?family=Lora:wght@400;700&display=swap">
<style>
  :root {
    --navy: #233f66;
    --green: #12543f;
    --card: #f4f4f2;
    --backdrop: #b9b9b9;
    --ink-soft: #3d4a5c;
    --white: #ffffff;
  }
  * { box-sizing: border-box; margin: 0; padding: 0; }
  html, body {
    width: 1200px; height: 576px; overflow: hidden;
    background: var(--backdrop);
    font-family: "Lora", Georgia, serif;
  }
  .canvas { position: relative; width: 1200px; height: 576px; }
  .card {
    position: absolute; top: 138px;
    width: 484px; height: 292px;
    background: var(--card);
    border-radius: 12px;
    overflow: hidden;
    box-shadow: 0 3px 6px rgba(0,0,0,0.18);
  }
  .card--front { left: 80px; }
  .card--back { left: 602px; }

  /* Front */
  .front-brand {
    position: absolute; left: 0; right: 0; top: 92px;
    text-align: center; color: var(--navy);
  }
  .front-brand .brand-mark {
    display: block; width: 40px; height: 40px; margin: 0 auto 14px;
    background: var(--green); border-radius: 50%;
  }
  .front-brand .brand-name {
    font-weight: 700; font-size: 34px; letter-spacing: 3px; line-height: 1;
  }
  .service-line {
    position: absolute; left: 0; right: 0; top: 258px;
    text-align: center; font-size: 12.5px; color: var(--navy);
  }
  .service-line .sep { margin: 0 5px; }
  .front-band {
    position: absolute; left: 0; right: 0; bottom: 0; height: 6px;
    background: linear-gradient(90deg, var(--green), var(--navy));
  }

  /* Back */
  .person { position: absolute; left: 24px; top: 48px; }
  .person-name {
    font-weight: 700; font-size: 21px; color: var(--navy); letter-spacing: 0.5px;
  }
  .person-creds { margin-top: 3px; font-size: 10.5px; color: var(--ink-soft); }
  .contact-list {
    position: absolute; left: 24px; top: 140px; list-style: none;
    font-size: 12.5px; color: var(--navy);
  }
  .contact-list li { display: flex; align-items: center; height: 18px; }
  .contact-list svg { width: 12px; height: 12px; margin-right: 12px; fill: var(--navy); }
  .social {
    position: absolute; left: 24px; top: 196px;
    display: flex; align-items: center; font-size: 13px; color: var(--navy);
  }
  .social-dot {
    width: 20px; height: 20px; border-radius: 50%; margin-left: 5px;
    background: var(--navy);
  }
  .social-dot:first-of-type { margin-left: 7px; }
  .back-brand {
    position: absolute; right: 24px; top: 96px; width: 210px;
    text-align: center; color: var(--navy);
    font-weight: 700; font-size: 25px; letter-spacing: 2px; line-height: 1;
  }
  .wave { position: absolute; left: 0; top: 0; width: 484px; height: 292px; }
  .slogan {
    position: absolute; right: 24px; top: 246px; text-align: right;
    font-size: 12.5px; line-height: 17px; color: var(--white);
  }
</style>
</head>
<body>
<main class="canvas">
  <section class="card card--front" aria-label="Card front">
    <div class="front-brand">
      <span class="brand-mark"></span>
      <div class="brand-name">VARDEN THERAPY</div>
    </div>
    <p class="service-line">Direct Billing<span class="sep">|</span>Services Including Physiotherapy<span class="sep">|</span>IMS<span class="sep">|</span>Acupuncture</p>
    <div class="front-band"></div>
  </section>

  <section class="card card--back" aria-label="Card back">
    <svg class="wave" viewBox="0 0 484 292" aria-hidden="true">
      <path fill="var(--green)" d="M0,220 C90,252 200,262 290,226 C360,198 420,178 484,170 L484,186 C420,192 360,212 290,240 C200,276 90,268 0,236 Z"/>
      <path fill="var(--navy)" d="M0,240 C90,276 200,284 290,250 C360,222 420,202 484,198 L484,292 L0,292 Z"/>
    </svg>

    <div class="person">
      <h1 class="person-name">LUKE VARDEN</h1>
      <p class="person-creds">BSc(kin), MPT, CAFCI, IMS</p>
    </div>

    <ul class="contact-list">
      <li><svg viewBox="0 0 12 12"><path d="M1 4c0-2 2-3 5-3s5 1 5 3v1H8V4H4v1H1z M3 6h6l1 5H2z"/></svg>867-555-0142</li>
      <li><svg viewBox="0 0 12 12"><path d="M0 2h12v8H0z M1 3v.5l5 3.5 5-3.5V3L6 6.2z" fill-rule="evenodd"/></svg>VardenTherapy@postnest.ca</li>
      <li><svg viewBox="0 0 12 12"><path d="M6 0a6 6 0 1 0 0 12A6 6 0 0 0 6 0zm0 1.2c.8.8 1.3 2.5 1.4 4.2H4.6C4.7 3.7 5.2 2 6 1.2zM4.6 6.6h2.8c-.1 1.7-.6 3.4-1.4 4.2-.8-.8-1.3-2.5-1.4-4.2zM1.2 5.4c.2-1.8 1.5-3.3 3.1-3.9-.5 1-.8 2.4-.9 3.9zm0 1.2h2.2c.1 1.5.4 2.9.9 3.9-1.6-.6-2.9-2.1-3.1-3.9zm9.6-1.2H8.6c-.1-1.5-.4-2.9-.9-3.9 1.6.6 2.9 2.1 3.1 3.9zm0 1.2c-.2 1.8-1.5 3.3-3.1 3.9.5-1 .8-2.4.9-3.9z"/></svg>www.VardenTherapy.ca</li>
    </ul>

    <div class="social">Follow us on:<span class="social-dot"></span><span class="social-dot"></span></div>

    <div class="back-brand">VARDEN<br>THERAPY</div>

    <p class="slogan">Mobile Physiotherapy<br>Your Road To Recovery</p>
  </section>
</main>
</body>
</html>
```